VELKO Website Redesign in Wix

Task:
Create a new design for all pages of the VELKO technology website in Wix. Specifications are:
Color palette preferences: black, white, gray, purple, blue. See VELKO Ref Doc provided.
Please refer to the VELKO_ref doc for a sample of the desired color palette
Typesetting must be in Montserrat
Brand will be that of a Marketing Technology company
Looking for vibrant, highly engaging images and organized, digestible flow. Open to suggestions
Required format is Wix.
VELKO logo does NOT need to be redesigned. Please use the files provided for the VELKO logo.
Look and feel
Each slider illustrates characteristics of the customer's brand and the style your logo design should communicate.

```html
<!DOCTYPE html>
<html lang="en">
<head>
<meta charset="utf-8">
<title>VELKO – Marketing Technology</title>
<link href="https://fonts.googleapis.com/css2?family=Montserrat:wght@500;600;700;800&family=Roboto:wght@400;500;700&display=swap" rel="stylesheet">
<style>
:root{
  --purple:#3b1d9c;
  --navy:#13063b;
  --ink:#111111;
  --text:#555555;
  --white:#ffffff;
  --line:#d9d9dc;
  --orange:#d2430f;
  --badge:#e3e3e7;
}
*{margin:0;padding:0;box-sizing:border-box}
html,body{width:1200px;height:3235px;overflow:hidden;background:var(--white)}
body{position:relative;font-family:'Roboto',sans-serif;color:var(--text)}
.abs{position:absolute}
.heading{font-family:'Montserrat',sans-serif;font-weight:700;color:var(--ink);text-transform:uppercase;letter-spacing:.2px}
.btn{position:absolute;display:flex;align-items:center;justify-content:center;gap:10px;background:var(--purple);color:var(--white);font-family:'Roboto',sans-serif;font-weight:700;font-size:14px;text-transform:uppercase;border-radius:2px}
.btn svg{width:13px;height:13px}
.para{font-size:15.5px;line-height:27.5px;text-align:justify}

/* hero */
.hero{left:0;top:0;width:1200px;height:624px;background:linear-gradient(110deg,#0a1d2c 0%,#15384a 40%,#2b5f72 70%,#34788a 100%)}
.hero-visual{left:0;top:40px;width:640px;height:584px;background:radial-gradient(ellipse at 55% 45%,rgba(90,150,170,.55),rgba(10,30,45,0) 65%)}
.brand{font-family:'Montserrat',sans-serif;font-weight:600;color:var(--white);letter-spacing:8px}
.nav a{position:absolute;top:38px;color:var(--white);font-weight:700;font-size:14px;text-decoration:none}
.hero-kicker{left:627px;top:210px;font-family:'Montserrat',sans-serif;font-weight:700;font-size:19px;color:var(--white)}
.hero-title{left:624px;top:232px;font-family:'Montserrat',sans-serif;font-weight:800;font-size:88px;line-height:100px;color:var(--white);letter-spacing:2px}
.hero-lead{left:627px;top:338px;width:490px;font-weight:700;font-size:15px;line-height:26px;color:var(--white)}

/* services */
.card{position:absolute;width:221px;height:250px;border-radius:15px;color:var(--white);text-align:center;padding-top:24px}
.card.purple{background:var(--purple)}
.card.navy{background:var(--navy)}
.card svg{width:64px;height:60px;display:block;margin:0 auto}
.card h3{font-family:'Roboto',sans-serif;font-size:15.5px;font-weight:700;margin-top:14px}
.card .dash{width:30px;height:2px;background:var(--white);margin:12px auto 14px}
.card p{font-size:13.5px;line-height:19px;padding:0 14px;text-align:justify;text-align-last:center}
.card .bar{position:absolute;left:29px;right:29px;bottom:24px;height:3px;background:var(--white)}

/* awards */
.award{position:absolute;width:220px;text-align:center;color:#222}
.award .badge{margin:0 auto;background:var(--badge)}
.award .cap{font-size:13px;line-height:16.5px;margin-top:10px}
.award .cap.small{font-size:8.5px;line-height:11px}
.award .big{font-size:20px;line-height:25px;margin-top:12px}

/* partners */
.partners{left:112px;top:2171px;width:975px;height:118px;border:1px solid var(--line);display:flex}
.partner{flex:1;border-right:1px solid var(--line);display:flex;align-items:center;justify-content:center;gap:10px;font-family:'Montserrat',sans-serif;font-weight:600;font-size:19px;color:#8a8a8a}
.partner:last-child{border-right:none}
.partner .mark{width:26px;height:26px;border-radius:50%;background:#bdbdbd}

/* footer */
.footer{left:0;top:2843px;width:1200px;height:392px;background:var(--navy);color:var(--white)}
.footer h4{position:absolute;top:77px;font-family:'Roboto',sans-serif;font-weight:700;font-size:13.5px}
.footer .links a,.footer .contact div{position:absolute;color:var(--white);text-decoration:none}
.footer .links a{font-size:14.5px}
.footer .contact div{font-size:16.5px}
.social{position:absolute;top:115px;width:32px;height:32px;border:1px solid rgba(255,255,255,.7);border-radius:50%}
</style>
</head>
<body>

<section class="abs hero">
  <div class="abs hero-visual" role="img" aria-label="Hand holding a tablet with a glowing globe and connected app icons floating above it"></div>
  <div class="abs brand" style="left:110px;top:20px;font-size:38px;">VELKO</div>
  <nav class="nav">
    <a style="left:395px">Home</a>
    <a style="left:463px">How it works</a>
    <a style="left:576px">VELKO Applications</a>
    <a style="left:724px">Company</a>
    <a style="left:816px">Contact Us</a>
  </nav>
  <div class="btn" style="left:935px;top:25px;width:151px;height:44px;">Get Started <svg viewBox="0 0 16 16"><circle cx="8" cy="8" r="8" fill="#fff"/><path d="M6 4.5 9.5 8 6 11.5" stroke="#3b1d9c" stroke-width="2" fill="none"/></svg></div>
  <div class="abs hero-kicker">WELCOME TO</div>
  <h1 class="abs hero-title">VELKO</h1>
  <p class="abs hero-lead">Increase and perfect your connection with consumers using VELKO™'s patented self-service content delivery technology</p>
  <div class="btn" style="left:627px;top:417px;width:152px;height:44px;">Get Started <svg viewBox="0 0 16 16"><circle cx="8" cy="8" r="8" fill="#fff"/><path d="M6 4.5 9.5 8 6 11.5" stroke="#3b1d9c" stroke-width="2" fill="none"/></svg></div>
</section>

<section class="strategy">
  <h2 class="abs heading" style="left:120px;top:808px;width:430px;font-size:26px;line-height:34px;">Strategy towards market dominance</h2>
  <p class="abs para" style="left:120px;top:892px;width:412px;">Lorem ipsum dolor sit amet, consectetur adipiscing elit, sed do eiusmod tempor incididunt ut labore et dolore magna aliqua. Ut enim ad minim veniam, quis nostrud exercitation ullamco laboris nisi ut aliquip ex ea commodo consequat. Duis aute irure dolor in reprehenderit in voluptate velit esse cillum dolore eu fugiat nulla pariatur. Excepteur sint occaecat cupidatat non proident, sunt in culpa qui officia deserunt mollit anim id est laborum.</p>
  <div class="btn" style="left:122px;top:1134px;width:150px;height:46px;">View All <svg viewBox="0 0 16 16"><circle cx="8" cy="8" r="8" fill="#fff"/><path d="M6 4.5 9.5 8 6 11.5" stroke="#3b1d9c" stroke-width="2" fill="none"/></svg></div>

  <div class="card purple" style="left:610px;top:700px;">
    <svg viewBox="0 0 64 60"><circle cx="26" cy="16" r="10" fill="#fff"/><path d="M6 50c0-12 9-20 20-20 5 0 9 1 12 4" fill="#fff"/><circle cx="44" cy="40" r="12" fill="#fff"/><path d="M44 33v14M37 40h14" stroke="#3b1d9c" stroke-width="3"/></svg>
    <h3>Corporate Subscription</h3><div class="dash"></div>
    <p>Sed ut perspiciatis unde omnis iste natus error sit voluptatem accusantium</p><div class="bar"></div>
  </div>
  <div class="card navy" style="left:858px;top:760px;">
    <svg viewBox="0 0 64 60"><rect x="10" y="6" width="44" height="34" fill="#fff"/><path d="M16 14h24M16 20h30M16 26h20" stroke="#13063b" stroke-width="2.5"/><circle cx="42" cy="38" r="8" fill="#fff" stroke="#13063b" stroke-width="2.5"/><path d="M38 44l-3 10 7-4 7 4-3-10" fill="#fff"/></svg>
    <h3>AD Tech Licensing</h3><div class="dash"></div>
    <p>Sed ut perspiciatis unde omnis iste natus error sit voluptatem accusantium</p><div class="bar"></div>
  </div>
  <div class="card navy" style="left:610px;top:983px;">
    <svg viewBox="0 0 64 60"><circle cx="32" cy="30" r="22" fill="#fff"/><path d="M32 8v44M10 30h44" stroke="#13063b" stroke-width="3"/></svg>
    <h3>Platform Integrations</h3><div class="dash"></div>
    <p>Sed ut perspiciatis unde omnis iste natus error sit voluptatem accusantium</p><div class="bar"></div>
  </div>
  <div class="card purple" style="left:858px;top:1043px;">
    <svg viewBox="0 0 64 60"><path d="M24 6c-10 0-16 8-16 16 0 7 4 10 6 14v8h20v-8c2-4 6-7 6-14 0-8-6-16-16-16z" fill="#fff"/><rect x="16" y="48" width="16" height="5" fill="#fff"/><circle cx="46" cy="18" r="9" fill="none" stroke="#fff" stroke-width="4"/></svg>
    <h3>Technology Licensing</h3><div class="dash"></div>
    <p>Sed ut perspiciatis unde omnis iste natus error sit voluptatem accusantium</p><div class="bar"></div>
  </div>
</section>

<section class="platform">
  <div class="abs" role="img" aria-label="Excited young woman in a yellow top and hat looking at her smartphone while holding a coffee cup" style="left:110px;top:1358px;width:463px;height:366px;background:linear-gradient(120deg,#d9d6d2 0%,#b9a08a 45%,#e3b640 85%,#d8d4cf 100%);"></div>
  <h2 class="abs heading" style="left:632px;top:1384px;font-size:26px;">Our revolutionary platform</h2>
  <p class="abs para" style="left:632px;top:1434px;width:458px;">Whether you're marketing software, selling a product, or looking to close a deal – find out your target market and quickly modify your campaigns to reach consumers silently and securely.</p>
  <p class="abs para" style="left:632px;top:1543px;width:458px;">Our platform goes far beyond basic ad optimization to deliver individualized content that immediately increases engagement over any communication medium with embedded tones.</p>
  <div class="btn" style="left:634px;top:1648px;width:150px;height:44px;">Learn More <svg viewBox="0 0 16 16"><circle cx="8" cy="8" r="8" fill="#fff"/><path d="M6 4.5 9.5 8 6 11.5" stroke="#3b1d9c" stroke-width="2" fill="none"/></svg></div>
</section>

<section class="awards">
  <h2 class="abs heading" style="left:0;top:1811px;width:1200px;text-align:center;font-size:26px;">Awards</h2>
  <div class="award" style="left:125px;top:1874px;">
    <div class="badge" style="width:64px;height:64px;border-radius:6px;" role="img" aria-label="Award badge"></div>
    <div class="cap">Northstar Founder of The<br>Year® 1995 Mountain<br>Desert Award Finalist</div>
  </div>
  <div class="award" style="left:376px;top:1872px;">
    <div class="badge" style="width:60px;height:82px;border-radius:50%;" role="img" aria-label="Award badge"></div>
    <div class="cap small" style="margin-top:12px;">Brightbulb Award – Gold Winner for<br>innovation in the category of "Lifestyle<br>and Social Impact: Quality of Life" in<br>2013 for SoundLens</div>
  </div>
  <div class="award" style="left:617px;top:1898px;">
    <div class="badge" style="width:140px;height:50px;border-radius:4px;" role="img" aria-label="Listing badge"></div>
    <div class="big">Market Ledger<br>30 under 30</div>
  </div>
  <div class="award" style="left:848px;top:1902px;">
    <div class="badge" style="width:140px;height:46px;border-radius:4px;" role="img" aria-label="Listing badge"></div>
    <div class="big" style="font-size:19px;line-height:24px;">Market Ledger<br>40 under 40</div>
  </div>
</section>

<section class="customers">
  <h2 class="abs heading" style="left:0;top:2102px;width:1200px;text-align:center;font-size:26px;">Our customers &amp; partners</h2>
  <div class="abs partners">
    <div class="partner">Galleria Coastline</div>
    <div class="partner"><span class="mark"></span>Vaultline</div>
    <div class="partner">Corvin &amp; Hale</div>
    <div class="partner"><span class="mark" style="border-radius:0;"></span>Greyshield Ltd</div>
  </div>
</section>

<section class="about">
  <h2 class="abs heading" style="left:109px;top:2406px;font-size:26px;">About us</h2>
  <p class="abs para" style="left:109px;top:2455px;width:458px;">VELKO™ Technology is a revolutionary platform that uses high frequency tones (known as VELKO packets) imperceptible to the human ear. VELKO's patented technology embeds information on an audio file for a more targeted, enhanced user experience via music, video, text, virtual reality, augmented reality, and other content. It is a modern-day solution to an age-old problem–establishing two-way communication with a consumer rather than listening to what they have to say.</p>
  <div class="btn" style="left:110px;top:2696px;width:152px;height:44px;">Learn More <svg viewBox="0 0 16 16"><circle cx="8" cy="8" r="8" fill="#fff"/><path d="M6 4.5 9.5 8 6 11.5" stroke="#3b1d9c" stroke-width="2" fill="none"/></svg></div>
  <div class="abs" role="img" aria-label="Group of five young friends sitting outdoors on a step, smiling and looking at phones and a tablet" style="left:625px;top:2381px;width:462px;height:366px;background:linear-gradient(160deg,#8aa06a 0%,#c9c6bd 35%,#4d5a6e 70%,#2f3440 100%);"></div>
</section>

<footer class="abs footer">
  <div class="abs brand" style="left:110px;top:68px;font-size:44px;letter-spacing:10px;">VELKO</div>
  <div class="contact">
    <div style="left:110px;top:140px;">1-800-555-0142</div>
    <div style="left:110px;top:170px;">hello@velko.example</div>
    <div style="left:110px;top:200px;">147 , Lorem Ipsum Dolor</div>
    <div style="left:110px;top:230px;">United States</div>
  </div>
  <h4 style="left:385px;">QUICK LINKS</h4>
  <div class="links">
    <a style="left:385px;top:107px;">Home</a>
    <a style="left:385px;top:141px;">How it works</a>
    <a style="left:385px;top:175px;">VELKO Applications</a>
    <a style="left:385px;top:209px;">Company</a>
    <a style="left:385px;top:244px;">Contact Us</a>
  </div>
  <h4 style="left:574px;">SUBSCRIBE TO OUR NEWSLETTER</h4>
  <div class="abs" style="left:574px;top:114px;width:248px;height:38px;background:#fff;border-radius:3px;color:#555;font-size:14px;padding:11px 10px;">Email *</div>
  <div class="abs" style="left:574px;top:167px;width:248px;height:37px;background:var(--orange);border-radius:3px;color:#fff;font-weight:700;font-size:13.5px;text-align:center;line-height:37px;">SUBMIT NOW</div>
  <h4 style="left:917px;">FOLLOW US ON</h4>
  <span class="social" style="left:918px;" aria-label="Social profile"></span>
  <span class="social" style="left:959px;" aria-label="Social profile"></span>
  <span class="social" style="left:1001px;" aria-label="Social profile"></span>
  <span class="social" style="left:1042px;" aria-label="Social profile"></span>
  <div class="abs" style="left:110px;top:316px;width:979px;height:1px;background:rgba(255,255,255,.6);"></div>
  <div class="abs" style="left:0;top:342px;width:1200px;text-align:center;font-size:14.5px;">©2022 VELKO™. All Rights Reserved</div>
</footer>

</body>
</html>
```